Gobal construction supply company needs new business card design

I need a business card design for my global supply company using an existing logo. i will be looking to print these on rounded corner cards with the black background version of my logo on the back. on the front white background, my logo again and my simple details.

```html
<!DOCTYPE html>
<html lang="en">
<head>
<meta charset="utf-8">
<title>Northgate Building Supplies – Business Card</title>
<link rel="stylesheet" href="https://fonts.googleapis.com/css2?family=Montserrat:wght@700&family=Open+Sans:wght@400&display=swap">
<style>
  :root {
    --stage: #5c5c5c;
    --card-light: #f2f2f2;
    --card-dark: #141414;
    --ink: #000000;
    --text: #2b2b2b;
    --accent: #d90000;
    --white: #ffffff;
  }
  * { box-sizing: border-box; margin: 0; padding: 0; }
  html, body { width: 1200px; height: 802px; overflow: hidden; background: var(--stage); }
  .stage { position: relative; width: 1200px; height: 802px; }

  .card {
    position: absolute; top: 274px; width: 442px; height: 265px;
    border-radius: 14px; overflow: hidden;
  }
  .card--front { left: 136px; background: var(--card-light); }
  .card--back { left: 624px; background: var(--card-dark); }

  /* front: side bands */
  .band { position: absolute; }
  .band--accent { left: 0; top: 0; width: 26px; height: 63px; background: var(--accent); }
  .band--lower { left: 0; top: 90px; width: 26px; height: 175px; background: var(--ink); }
  .band--gap { left: 26px; top: 0; width: 31px; height: 265px; background: var(--white); }
  .band--wide { left: 57px; top: 0; width: 71px; height: 265px; background: var(--ink); }

  /* front: brand */
  .front-brand { position: absolute; left: 153px; top: 0; display: flex; align-items: center; gap: 12px; }
  .front-brand__dot { width: 84px; height: 84px; border-radius: 50%; background: var(--accent); }
  .front-brand__name { font: 700 16px/1 "Montserrat", sans-serif; color: var(--ink); letter-spacing: 0.5px; }

  /* front: details */
  .person { position: absolute; left: 201px; top: 137px; }
  .person__name { font: 700 16px/1 "Montserrat", sans-serif; color: var(--accent); }
  .person__role { margin-top: 2px; font: 400 13px/1.1 "Open Sans", sans-serif; color: var(--text); }
  .contact { position: absolute; left: 201px; top: 175px; list-style: none; }
  .contact__item {
    display: flex; align-items: center; height: 15.8px;
    font: 400 13px "Open Sans", sans-serif; color: var(--text);
  }
  .contact__icon { width: 9px; height: 9px; margin-right: 6px; fill: var(--accent); flex: none; }

  /* back */
  .back-brand {
    position: absolute; left: 0; right: 0; top: 121px; text-align: center;
    font: 700 19px/1 "Montserrat", sans-serif; color: var(--white); letter-spacing: 0.3px;
  }
</style>
</head>
<body>
<main class="stage">
  <section class="card card--front" aria-label="Business card front">
    <div class="band band--accent"></div>
    <div class="band band--lower"></div>
    <div class="band band--gap"></div>
    <div class="band band--wide"></div>

    <div class="front-brand">
      <div class="front-brand__dot"></div>
      <div class="front-brand__name">NORTHGATE</div>
    </div>

    <div class="person">
      <h1 class="person__name">DANIEL CARTER</h1>
      <p class="person__role">Managing Director</p>
    </div>
    <ul class="contact">
      <li class="contact__item">
        <svg class="contact__icon" viewBox="0 0 10 10"><path d="M0 4 Q5 0 10 4 L10 5 L7.5 5 L7 3.5 L3 3.5 L2.5 5 L0 5 Z M2 6 L8 6 L9 10 L1 10 Z"/></svg>
        040-555 012 345
      </li>
      <li class="contact__item">
        <svg class="contact__icon" viewBox="0 0 10 10"><path d="M2.5 0 H7.5 V10 H2.5 Z M3.5 1 V8 H6.5 V1 Z"/></svg>
        040-555 012 345
      </li>
      <li class="contact__item">
        <svg class="contact__icon" viewBox="0 0 10 10"><path d="M0 2 H10 V8 H0 Z"/><path d="M0 2 L5 5.5 L10 2" fill="none" stroke="#f2f2f2" stroke-width="1"/></svg>
        hello@northgatesupply.com
      </li>
      <li class="contact__item">
        <svg class="contact__icon" viewBox="0 0 10 10"><circle cx="5" cy="5" r="5"/><path d="M3 3 Q5 2 6 4 Q4 5 5 7 Q3 6 3 3 Z" fill="#f2f2f2"/></svg>
        www.northgatesupply.com
      </li>
    </ul>
  </section>

  <section class="card card--back" aria-label="Business card back">
    <h2 class="back-brand">NORTHGATE BUILDING SUPPLIES</h2>
  </section>
</main>
</body>
</html>
```